Design Brief for Website Redesign

Client Name: Harbourline IT
Website: www.harbourlineit.com.au
Industry: Managed IT Services
Target Audience: Small to medium-sized businesses in Australia, requiring IT solutions, IT support, cloud services, and phone systems.

Project Overview
We are seeking a full redesign of the Harbourline IT website to modernize its look, improve usability, and enhance user experience across devices. The goal is to create a professional, clean, and user-friendly website that reflects our expertise in IT services and appeals to our business clients.

Objectives
Modern Visual Identity: Create a fresh, modern design that aligns with Harbourline IT's branding.

Improved User Experience: Simplify navigation, improve accessibility, and enhance mobile responsiveness.

Clear Calls to Action: Ensure CTAs are prominent and encourage user engagement.

Enhanced Trust & Credibility: Highlight testimonials, case studies, and industry credentials.

SEO Optimization: Ensure the site is optimized for search engines, including proper heading structures and metadata.
Design Style & Tone
Professional: Clean, modern, and polished to reflect our IT expertise.

Minimalist: Simple layouts, plenty of white space, and easy-to-read typography.

Tech-focused: Subtle tech-themed design elements that reinforce our brand as a leading IT service provider.

Colors: Use our existing brand colors, or propose a color scheme that complements the tech industry while maintaining a professional feel.

Typography: Clear, readable fonts that convey professionalism and trustworthiness.

Key Pages & Features
Home Page:

Hero section with a clear value proposition.

Highlight key services (IT support, cloud solutions, phone systems, etc.) with icons and brief descriptions.

Prominent CTAs (e.g., “Request a Quote,” “Book a Demo”).

Testimonials from satisfied clients.

Services Page:

Detailed breakdown of the services we offer (IT support, cloud services, phone systems, etc.).

Use of icons or illustrations to make the services visually engaging.

Clear CTAs to request quotes or book consultations.

About Us Page:

Information about our company history, mission, and team.

Highlight our certifications, partnerships, and industry expertise.

Case Studies/Testimonials Page:

Showcase client success stories and testimonials with visuals and brief case study summaries.

Include a trust-building section with logos of major clients or partners.

Contact Page:

Simple contact form for inquiries.

Integrated map with office location.

Social media links and phone number.

Blog/Resource Section:

Easy-to-navigate blog section for IT-related articles, tips, and industry news.

Clear categorization and tags for easy browsing.

Knowledge Base/Support Page:

Self-service area for clients to find articles, FAQs, and support guides.

Option to submit a support ticket.

Mobile Responsiveness:

Ensure the design is fully responsive, with no horizontal scrolling or misaligned content on mobile.

Functional Requirements
Fast Load Times: Optimize images, minimize unnecessary scripts, and ensure the site loads quickly on both desktop and mobile.

User-Friendly CMS: We need a CMS that is easy to update (preferably WordPress, but open to other suggestions).

SEO Best Practices: Structure the site with proper metadata, alt tags, and semantic HTML for better search engine optimization.

Security: Ensure the website follows security best practices (SSL, HTTPS).

Deliverables
Full website design (desktop and mobile versions).

Design mockups in Photoshop, Sketch, or Figma (whichever is preferred).

Working prototype (optional).

Final website files, including images and assets.

A style guide for ongoing consistency.

Industry/Entity Type

IT Managed Services

Number of Pages Required

3 page

Requirements
Must have
• EXCELLENT UX/UI

```html
<!DOCTYPE html>
<html lang="en">
<head>
<meta charset="utf-8">
<title>Harbourline IT | Managed IT Services Sydney</title>
<link href="https://fonts.googleapis.com/css2?family=Lexend:wght@400;500;600&family=Poppins:wght@400;500;600&display=swap" rel="stylesheet">
<style>
:root{
  --red:#e8233f;
  --ink:#1c1c1c;
  --text:#3a3a3a;
  --muted:#f5f5f5;
  --dark:#1b1b1b;
  --white:#fff;
}
*{box-sizing:border-box;margin:0;padding:0}
html,body{width:1200px;height:3027px;overflow:hidden}
body{font-family:'Poppins',sans-serif;color:var(--ink);background:var(--white);position:relative}
a{color:inherit;text-decoration:none}
.abs{position:absolute}

/* top bar */
.topbar{position:absolute;left:0;top:0;width:1200px;height:54px;background:var(--muted)}
.topbar .contact{position:absolute;top:16px;font-size:14px;color:var(--text);display:flex;align-items:center;gap:8px}
.topbar .sep{position:absolute;left:709px;top:15px;font-size:14px;color:var(--text)}
.social-top{position:absolute;left:977px;top:0;display:flex}
.social-top span{width:37px;height:54px;border-left:1px solid #ddd;display:block}
.social-top span.active{background:var(--red)}
.social-top span:last-child{border-right:1px solid #ddd}

/* header */
.header{position:absolute;left:0;top:54px;width:1200px;height:94px;background:var(--white)}
.brand{position:absolute;font-family:'Poppins',sans-serif;font-weight:600;color:var(--red);white-space:nowrap;letter-spacing:-0.5px}
.header .brand{left:112px;top:22px;font-size:38px}
.nav{position:absolute;left:433px;top:33px;display:flex;gap:23px;font-size:16px;font-weight:500}
.nav a.current{color:var(--red);border-bottom:2px solid var(--red);padding-bottom:2px}
.btn{position:absolute;background:var(--red);color:var(--white);font-weight:600;font-size:15px;border-radius:24px;display:flex;align-items:center;justify-content:center}

/* hero */
.hero{position:absolute;left:0;top:148px;width:1200px;height:601px;background:radial-gradient(ellipse at 55% 35%,#4f5a66 0%,#2a3038 45%,#14181d 100%)}
.hero h1{position:absolute;left:0;width:1200px;top:262px;text-align:center;font-family:'Lexend',sans-serif;font-weight:500;font-size:42px;line-height:52px;color:var(--white)}
.hero p{position:absolute;left:250px;width:700px;top:378px;text-align:center;font-size:19.5px;line-height:28.5px;color:var(--white)}
.hero-dots{position:absolute;left:1138px;top:459px}
.hero-dots i{display:block;width:12px;height:12px;border:2px solid var(--white);border-radius:50%;margin-bottom:8px}
.hero-dots i.on{background:var(--white)}

/* headings */
.sec-title{position:absolute;font-family:'Lexend',sans-serif;font-weight:500;font-size:38px;color:var(--ink)}
.rule{position:absolute;height:3px;width:76px;background:var(--red)}

/* about */
.about-sub{position:absolute;left:112px;width:490px;font-family:'Lexend',sans-serif;font-size:18.5px;line-height:28px;color:var(--ink)}
.about-text{position:absolute;left:112px;width:483px;font-size:15.5px;line-height:25px;text-align:justify;color:var(--text)}
.about-visual{position:absolute;left:650px;top:867px;width:438px;height:475px;background:linear-gradient(160deg,#f58a9a 0%,#e8233f 55%,#c51430 100%)}

/* services */
.services{position:absolute;left:0;top:1449px;width:1200px;height:631px;background:var(--muted)}
.card{position:absolute;top:1616px;width:302px;height:384px;border-radius:26px;background:#fbfbfb}
.card.featured{background:var(--white);box-shadow:0 10px 30px rgba(0,0,0,.12)}
.card .icon{position:absolute;left:24px;top:32px;width:90px;height:90px;border-radius:50%;background:var(--red);display:flex;align-items:center;justify-content:center}
.card h3{position:absolute;left:24px;top:140px;font-family:'Lexend',sans-serif;font-weight:500;font-size:20px}
.card p{position:absolute;left:25px;top:178px;width:255px;font-size:15px;line-height:24px;color:var(--text)}
.card .more{position:absolute;left:25px;top:333px;font-size:15px;color:var(--red);border-bottom:1px solid var(--red)}
.arrow{position:absolute;top:1787px;width:41px;height:41px;border-radius:50%;display:flex;align-items:center;justify-content:center}

/* testimonials */
.tcard{position:absolute;top:2258px;width:407px;height:263px;border-radius:30px;background:var(--white);box-shadow:0 8px 26px rgba(0,0,0,.12)}
.avatar{position:absolute;top:2342px;width:94px;height:94px;border-radius:50%;background:linear-gradient(150deg,#9aa57a,#5d5a4c)}
.tcard .quote{position:absolute;left:80px;top:34px}
.tcard p{position:absolute;left:80px;top:70px;width:305px;font-size:14px;line-height:21.5px;color:var(--text)}
.tcard .name{position:absolute;left:80px;top:200px;font-family:'Lexend',sans-serif;font-weight:500;font-size:16px}
.tcard .stars{position:absolute;left:80px;top:224px;font-size:11px;color:#f5a300;letter-spacing:1px}
.t-dots{position:absolute;left:564px;top:2563px;display:flex;gap:8px}
.t-dots i{width:12px;height:12px;border:1.5px solid var(--red);border-radius:50%}
.t-dots i.on{background:var(--red)}

/* footer */
.footer{position:absolute;left:0;top:2652px;width:1200px;height:325px;background:var(--dark);color:var(--white)}
.footer .brand{left:112px;top:168px;font-size:40px}
.f-head{position:absolute;top:62px;font-family:'Lexend',sans-serif;font-weight:600;font-size:17px}
.f-links{position:absolute;left:385px;top:106px;list-style:none;font-size:15px}
.f-links li{display:flex;align-items:center;gap:17px;height:43px}
.f-contact{position:absolute;left:571px;font-size:14px}
.f-contact b{display:block;font-weight:500;font-size:14.5px}
.f-contact small{font-size:12.5px}
.f-contact svg{position:absolute;left:0;top:2px}
.f-contact div{padding-left:34px}
.newsletter{position:absolute;left:805px;top:110px;width:284px;height:48px;background:var(--white);border:2px solid #fff}
.newsletter span{position:absolute;left:16px;top:13px;font-size:14px;color:#666}
.newsletter b{position:absolute;right:2px;top:2px;width:104px;height:40px;background:var(--red);font-size:14px;font-weight:600;display:flex;align-items:center;justify-content:center}
.f-social{position:absolute;left:805px;top:181px;display:flex;gap:5px}
.f-social i{width:34px;height:34px;border-radius:50%;border:1px solid #777;display:block}
.f-social i.on{background:var(--red);border-color:var(--red)}
.bottombar{position:absolute;left:0;top:2977px;width:1200px;height:50px;background:var(--red);color:var(--white);font-size:14px;display:flex;align-items:center;justify-content:center}
</style>
</head>
<body>

<div class="topbar">
  <div class="contact" style="left:586px"><svg width="12" height="12" viewBox="0 0 24 24"><path fill="#e8233f" d="M6.6 10.8a15 15 0 0 0 6.6 6.6l2.2-2.2c.3-.3.7-.4 1-.2 1.1.4 2.3.6 3.6.6.6 0 1 .4 1 1V20c0 .6-.4 1-1 1A17 17 0 0 1 3 4c0-.6.4-1 1-1h3.5c.6 0 1 .4 1 1 0 1.3.2 2.5.6 3.6.1.3 0 .7-.2 1z"/></svg>1300 555 010</div>
  <span class="sep">|</span>
  <div class="contact" style="left:734px"><svg width="14" height="11" viewBox="0 0 24 18"><path fill="#e8233f" d="M0 0h24v3l-12 8L0 3zM0 6l12 8 12-8v12H0z"/></svg>sales@harbourlineit.com.au</div>
  <div class="social-top"><span class="active" aria-label="Social profile one"></span><span aria-label="Social profile two"></span><span aria-label="Social profile three"></span></div>
</div>

<header class="header">
  <div class="brand">Harbourline IT</div>
  <nav class="nav"><a class="current">Home</a><a>Services</a><a>About Us</a><a>Case Studies</a><a>Contact</a></nav>
  <a class="btn" style="left:908px;top:21px;width:180px;height:44px">Request a Quote</a>
</header>

<section class="hero" role="img" aria-label="Technician working on a laptop in a server room">
  <h1>TECHNOLOGY SOLUTIONS FOR<br>A BETTER BUSINESS</h1>
  <p>We understand that technology is a critical component of running a successful business, and that's why we're here to help you navigate the ever-changing landscape of IT.</p>
  <a class="btn" style="left:524px;top:488px;width:152px;height:43px">Book a Demo</a>
  <div class="hero-dots"><i></i><i class="on"></i><i></i><i></i></div>
</section>

<h2 class="sec-title" style="left:112px;top:884px">ABOUT US</h2>
<div class="rule" style="left:112px;top:931px"></div>
<p class="about-sub" style="top:957px">Innovative Technology Solutions for Better Business: Your Managed IT Services Provider in Sydney</p>
<p class="about-sub" style="top:1020px">Your Trusted IT Company for Managed IT Services Sydney</p>
<p class="about-text" style="top:1088px">We're Harbourline IT, a Managed IT Services in Sydney provider. We offer expert IT Solutions and Support for Small and Medium Businesses.</p>
<p class="about-text" style="top:1175px">We are committed to listening to you, understanding your business needs, and providing IT Strategy and Support that aligns with your company's culture and bottom line.</p>
<a class="btn" style="left:457px;top:1275px;width:138px;height:44px">Learn More</a>
<div class="about-visual" role="img" aria-label="Red-toned photo of a team collaborating in the office"></div>

<section class="services"></section>
<h2 class="sec-title" style="left:0;width:1200px;text-align:center;top:1520px">OUR SERVICES</h2>
<div class="rule" style="left:562px;top:1569px"></div>

<div class="arrow" style="left:39px;border:1.5px solid var(--red)"><svg width="12" height="14" viewBox="0 0 12 14"><path d="M8 1 2 7l6 6" fill="none" stroke="#1c1c1c" stroke-width="2"/></svg></div>
<div class="arrow" style="left:1121px;background:var(--red)"><svg width="12" height="14" viewBox="0 0 12 14"><path d="m4 1 6 6-6 6" fill="none" stroke="#fff" stroke-width="2"/></svg></div>

<article class="card" style="left:112px">
  <div class="icon"><svg width="48" height="48" viewBox="0 0 48 48" fill="none" stroke="#fff" stroke-width="2"><circle cx="28" cy="18" r="6"/><circle cx="28" cy="18" r="11" stroke-dasharray="4 3"/><path d="M4 34h8l8 3h10l10-6M12 32v10H4"/></svg></div>
  <h3>IT Support</h3>
  <p>IT support is the backbone of any organisation. Regardless of how big or small a business is, having a dedicated IT support team is crucial to safeguard your systems.</p>
  <a class="more">Learn More</a>
</article>
<article class="card featured" style="left:449px">
  <div class="icon"><svg width="48" height="48" viewBox="0 0 48 48" fill="none" stroke="#fff" stroke-width="2"><path d="M12 38a8 8 0 0 1 0-16 12 12 0 0 1 23-2 9 9 0 0 1 1 18z"/><path d="M24 14v-6M14 16l-3-4M34 16l3-4"/><path d="m19 30 4 4 7-8"/></svg></div>
  <h3>Cloud Solutions</h3>
  <p>Since 1997, we've supported Australian businesses in cities from Sydney, Melbourne, to Brisbane in diverse industries such as real estate, industrial, retail, and legal services.</p>
  <a class="more">Learn More</a>
</article>
<article class="card" style="left:785px">
  <div class="icon"><svg width="48" height="48" viewBox="0 0 48 48" fill="none" stroke="#fff" stroke-width="2"><rect x="14" y="6" width="20" height="36" rx="3"/><path d="M21 37h6"/><circle cx="24" cy="19" r="4"/><path d="M18 29a6 6 0 0 1 12 0"/></svg></div>
  <h3>Phone Systems</h3>
  <p>Our inhouse design and development team create innovative, eye catching websites and apps. Whether it's a basic landing page or a major app project we can help</p>
  <a class="more">Learn More</a>
</article>

<h2 class="sec-title" style="left:0;width:1200px;text-align:center;top:2163px">TESTIMONIALS</h2>
<div class="rule" style="left:562px;top:2212px"></div>

<article class="tcard" style="left:180px">
  <svg class="quote" width="27" height="22" viewBox="0 0 27 22"><path fill="#e8233f" d="M0 22V12C0 5 4 1 11 0v4c-4 1-5 3-5 6h5v12zm16 0V12c0-7 4-11 11-12v4c-4 1-5 3-5 6h5v12z"/></svg>
  <p>I wish to thank Harbourline IT for their outstanding services &amp; for looking after our business. The services they provide make the daily operation of our business very smooth. We would have not survived without them.</p>
  <div class="name">- DANA WHITLOCK</div>
  <div class="stars">★★★★★</div>
</article>
<div class="avatar" style="left:137px" role="img" aria-label="Client portrait"></div>

<article class="tcard" style="left:666px">
  <svg class="quote" width="27" height="22" viewBox="0 0 27 22"><path fill="#e8233f" d="M0 22V12C0 5 4 1 11 0v4c-4 1-5 3-5 6h5v12zm16 0V12c0-7 4-11 11-12v4c-4 1-5 3-5 6h5v12z"/></svg>
  <p>I wish to thank Harbourline IT for their outstanding services &amp; for looking after our business. The services they provide make the daily operation of our business very smooth. We would have not survived without them.</p>
  <div class="name">- DANA WHITLOCK</div>
  <div class="stars">★★★★★</div>
</article>
<div class="avatar" style="left:624px" role="img" aria-label="Client portrait"></div>

<div class="t-dots"><i></i><i class="on"></i><i></i><i></i></div>

<footer class="footer">
  <div class="brand">Harbourline IT</div>
  <div class="f-head" style="left:385px">QUICK LINKS</div>
  <ul class="f-links">
    <li><svg width="13" height="13" viewBox="0 0 14 14"><circle cx="7" cy="7" r="7" fill="#e8233f"/><path d="M4 7h5M7 4l3 3-3 3" stroke="#1b1b1b" stroke-width="1.6" fill="none"/></svg>Home</li>
    <li><svg width="13" height="13" viewBox="0 0 14 14"><circle cx="7" cy="7" r="7" fill="#e8233f"/><path d="M4 7h5M7 4l3 3-3 3" stroke="#1b1b1b" stroke-width="1.6" fill="none"/></svg>Services</li>
    <li><svg width="13" height="13" viewBox="0 0 14 14"><circle cx="7" cy="7" r="7" fill="#e8233f"/><path d="M4 7h5M7 4l3 3-3 3" stroke="#1b1b1b" stroke-width="1.6" fill="none"/></svg>About Us</li>
    <li><svg width="13" height="13" viewBox="0 0 14 14"><circle cx="7" cy="7" r="7" fill="#e8233f"/><path d="M4 7h5M7 4l3 3-3 3" stroke="#1b1b1b" stroke-width="1.6" fill="none"/></svg>Case Studies</li>
    <li><svg width="13" height="13" viewBox="0 0 14 14"><circle cx="7" cy="7" r="7" fill="#e8233f"/><path d="M4 7h5M7 4l3 3-3 3" stroke="#1b1b1b" stroke-width="1.6" fill="none"/></svg>Contact</li>
  </ul>
  <div class="f-head" style="left:571px">CONTACT INFO</div>
  <div class="f-contact" style="top:104px"><svg width="11" height="15" viewBox="0 0 12 16"><path fill="#e8233f" d="M6 0a6 6 0 0 1 6 6c0 4-6 10-6 10S0 10 0 6a6 6 0 0 1 6-6zm0 3.5a2.5 2.5 0 1 0 0 5 2.5 2.5 0 0 0 0-5z"/></svg><div><b>ADDRESS:</b><small>Sydney, Australia</small></div></div>
  <div class="f-contact" style="top:159px"><svg width="13" height="13" viewBox="0 0 24 24"><path fill="#e8233f" d="M6.6 10.8a15 15 0 0 0 6.6 6.6l2.2-2.2c.3-.3.7-.4 1-.2 1.1.4 2.3.6 3.6.6.6 0 1 .4 1 1V20c0 .6-.4 1-1 1A17 17 0 0 1 3 4c0-.6.4-1 1-1h3.5c.6 0 1 .4 1 1 0 1.3.2 2.5.6 3.6.1.3 0 .7-.2 1z"/></svg><div><b>PHONE:</b><small>1300 555 010</small></div></div>
  <div class="f-contact" style="top:215px"><svg width="15" height="11" viewBox="0 0 24 18"><path fill="#e8233f" d="M0 0h24v3l-12 8L0 3zM0 6l12 8 12-8v12H0z"/></svg><div><b>EMAIL:</b><small>sales@harbourlineit.com.au</small></div></div>
  <div class="f-head" style="left:805px">NEWSLETTER SIGNUP</div>
  <div class="newsletter"><span>Email Address</span><b>SIGN UP</b></div>
  <div class="f-social"><i class="on" aria-label="Social profile one"></i><i aria-label="Social profile two"></i><i aria-label="Social profile three"></i></div>
</footer>
<div class="bottombar">© 2025 Harbourline IT &nbsp;&nbsp;|&nbsp;&nbsp; All Rights Reserved</div>

</body>
</html>
```